Venture 482 - Lumora Book Cover

I am looking for a Lumora book cover for my book about "Venture 482".
The Book is Titled:
Venture 482 Ascended
Shaping Outcomes: Paths To Unlocking Cosmic Truths
Author is Dorian Pell
Here is a book description that may help you understand more about it:
Inspired by the genius of Edwin Marlowe, this comprehensive guide delves into the ancient wisdom and cutting-edge science behind the 482 method, a powerful tool for manifesting your desires. Whether you're seeking personal growth, financial success, or spiritual enlightenment, this book provides advanced techniques and methods to transform your dreams into reality.
Any questions please ask.
Thanks
Owen

```html
<!DOCTYPE html>
<html lang="en">
<head>
<meta charset="UTF-8">
<title>Venture 482 Ascended — Dorian Pell</title>
<link rel="stylesheet" href="https://fonts.googleapis.com/css2?family=Josefin+Sans:wght@300;400&family=League+Spartan:wght@700;800&family=Montserrat:wght@400&display=swap">
<style>
  :root {
    --page-bg: #e8e8e6;
    --sky-top: #173038;
    --sky-mid: #5f8d99;
    --sky-low: #a8d0db;
    --floor: #9cc3cf;
    --author: #f4ddd0;
    --title-word: #fde9d9;
    --title-number: #e5f3fc;
    --edition: #3c4896;
    --subtitle: #1d2930;
    --figure-dark: #2f3a44;
    --figure-light: #4f6a80;
  }
  * { margin: 0; padding: 0; box-sizing: border-box; }
  html, body {
    width: 1200px;
    height: 1131px;
    overflow: hidden;
    background: var(--page-bg);
  }
  .book-cover {
    position: absolute;
    left: 235px;
    top: 20px;
    width: 730px;
    height: 1090px;
    overflow: hidden;
    background: linear-gradient(180deg, var(--sky-top) 0%, #2f5560 18%, var(--sky-mid) 45%, var(--sky-low) 72%, var(--floor) 100%);
  }
  .sky-glow {
    position: absolute;
    inset: 0;
    background: radial-gradient(ellipse 70% 40% at 55% 68%, rgba(210, 235, 242, 0.55), rgba(210, 235, 242, 0) 70%);
  }
  .floor {
    position: absolute;
    left: 0;
    right: 0;
    bottom: 0;
    height: 150px;
    background: linear-gradient(180deg, rgba(170, 206, 216, 0) 0%, rgba(150, 190, 202, 0.7) 100%);
  }
  .author {
    position: absolute;
    top: 48px;
    width: 100%;
    text-align: center;
    font-family: "Josefin Sans", sans-serif;
    font-weight: 300;
    font-size: 46px;
    letter-spacing: 14px;
    padding-left: 14px;
    color: var(--author);
  }
  .title {
    position: absolute;
    top: 172px;
    left: 0;
    width: 100%;
    text-align: center;
    font-family: "League Spartan", sans-serif;
  }
  .title-word {
    display: block;
    margin-left: 34px;
    font-weight: 800;
    font-size: 100px;
    line-height: 90px;
    letter-spacing: -4px;
    color: var(--title-word);
    text-shadow: 0 6px 14px rgba(0, 0, 0, 0.35);
  }
  .title-number {
    display: block;
    margin-left: 34px;
    margin-top: 2px;
    font-weight: 700;
    font-size: 290px;
    line-height: 230px;
    letter-spacing: -6px;
    color: var(--title-number);
    text-shadow: 0 10px 18px rgba(0, 0, 0, 0.3);
  }
  .edition {
    position: absolute;
    top: 492px;
    left: 30px;
    width: 100%;
    text-align: center;
    font-family: "Josefin Sans", sans-serif;
    font-weight: 400;
    font-size: 58px;
    letter-spacing: 22px;
    color: var(--edition);
    -webkit-text-stroke: 1.5px var(--edition);
  }
  .figure {
    position: absolute;
    left: 94px;
    top: 574px;
    width: 218px;
    height: 463px;
    border-radius: 60px 60px 20px 20px;
    background: linear-gradient(180deg, var(--figure-dark) 0%, var(--figure-dark) 60%, var(--figure-light) 100%);
    opacity: 0.85;
  }
  .subtitle {
    position: absolute;
    left: 360px;
    top: 728px;
    width: 265px;
    text-align: center;
    color: var(--subtitle);
  }
  .subtitle-main {
    font-family: "Josefin Sans", sans-serif;
    font-weight: 400;
    font-size: 29px;
    line-height: 36px;
    text-transform: uppercase;
  }
  .subtitle-tagline {
    margin-top: 24px;
    font-family: "Montserrat", sans-serif;
    font-weight: 400;
    font-size: 25px;
    line-height: 33px;
  }
</style>
</head>
<body>
  <main class="book-cover">
    <div class="sky-glow"></div>
    <div class="floor"></div>

    <p class="author">DORIAN PELL</p>

    <h1 class="title">
      <span class="title-word">VENTURE</span>
      <span class="title-number">482</span>
    </h1>
    <p class="edition">ASCENDED</p>

    <div class="figure" role="img" aria-label="Photo of a man in a dark coat and jeans, hands on hips, looking up at the sky"></div>

    <div class="subtitle">
      <p class="subtitle-main">Shaping<br>Outcomes:</p>
      <p class="subtitle-tagline">Paths to<br>unlocking<br>cosmic truths</p>
    </div>
  </main>
</body>
</html>
```